VKT Consulting

Government/Entitlement Consulting Services- I assist developers obtain entitlements from local, state and federal government agencies so that they can build their projects. Often these projects are very complicated and political and may face community opposition.

Target Market(s)

Real Estate Developers

Industry/Entity Type

Business Consultant

Contact Information for Business Card

Dana Melbrook
Principal

Font styles to use
Serif
Sans Serif

Requirements
Must have
• Classy and professional appeal.
Nice to have
• I like a combination of a mat and glossy finish. I've seen that done with black and then a bold color for a pop, but am not 100% committed to that.

```html
<!DOCTYPE html>
<html lang="en">
<head>
<meta charset="utf-8">
<title>VKT Consulting — Business Card</title>
<link rel="stylesheet" href="https://fonts.googleapis.com/css2?family=Arimo:wght@400;500;700&display=swap">
<style>
  :root {
    --bg: #e9e7e3;
    --card-white: #f7f7f7;
    --card-white-edge: #e6e6e6;
    --ink: #111111;
    --slate: #2f2f31;
    --slate-dark: #232325;
    --accent: #2aa6c4;
    --accent-light: #52c0da;
    --text-light: #f2f2f2;
  }
  * { margin: 0; padding: 0; box-sizing: border-box; }
  html, body { width: 1200px; height: 858px; overflow: hidden; }
  body {
    background: var(--bg);
    font-family: "Arimo", Arial, sans-serif;
    position: relative;
  }
  .card {
    position: absolute;
    top: 279px;
    width: 520px;
    height: 300px;
    border-radius: 3px;
    overflow: hidden;
    box-shadow: 0 10px 24px rgba(0,0,0,0.18), 0 2px 4px rgba(0,0,0,0.12);
  }
  .card--front { left: 40px; background: var(--card-white); }
  .card--back {
    left: 640px;
    background: radial-gradient(ellipse at 45% 40%, #ffffff 0%, var(--card-white) 55%, var(--card-white-edge) 100%);
  }

  .front__head {
    position: absolute; left: 0; top: 0; width: 100%; height: 104px;
    background: linear-gradient(180deg, #ffffff 0%, var(--card-white) 100%);
  }
  .front__company {
    position: absolute; left: 48px; top: 48px;
    font-size: 34px; font-weight: 700; letter-spacing: -0.5px;
    color: var(--ink);
  }
  .front__body {
    position: absolute; left: 0; top: 104px; width: 100%; height: 196px;
    background: linear-gradient(180deg, var(--slate) 0%, var(--slate-dark) 100%);
  }
  .front__accent { position: absolute; left: 0; top: 0; width: 100%; height: 100%; }

  .person {
    position: absolute; left: 48px; top: 70px;
    color: var(--text-light);
  }
  .person__name { font-size: 25px; font-weight: 400; }
  .person__title { font-size: 19px; text-align: right; margin-top: 1px; }

  .contact {
    position: absolute; left: 312px; top: 28px;
    list-style: none; color: var(--text-light);
    font-size: 16px; line-height: 25px;
  }

  .back__company {
    position: absolute; left: 0; top: 0; width: 100%; height: 100%;
    display: flex; align-items: center; justify-content: center;
    font-size: 50px; font-weight: 500; letter-spacing: -1px;
    color: var(--ink);
  }
</style>
</head>
<body>

<section class="card card--front" aria-label="Business card front">
  <div class="front__head">
    <div class="front__company">VKT Consulting</div>
  </div>
  <div class="front__body">
    <svg class="front__accent" viewBox="0 0 520 196" aria-hidden="true">
      <polygon points="248,0 290,0 262,196 220,196" fill="var(--accent)"/>
      <polygon points="248,0 290,0 285,35 243,35" fill="var(--accent-light)" opacity="0.5"/>
      <g fill="none" stroke="#ffffff" stroke-width="1.8" stroke-linecap="round" stroke-linejoin="round">
        <!-- web -->
        <circle cx="266" cy="40" r="8"/>
        <path d="M258 40 H274 M266 32 C262 36 262 44 266 48 M266 32 C270 36 270 44 266 48"/>
        <!-- email -->
        <circle cx="260" cy="82" r="4"/>
        <path d="M264 82 v2 a3 3 0 0 0 5 -2 a9 9 0 1 0 -4 7"/>
        <!-- phone -->
        <path d="M249 118 c0 8 6 14 14 14 l3 -4 -4 -3 -2 2 c-3 -1 -5 -3 -6 -6 l2 -2 -3 -4 z"/>
        <!-- home -->
        <path d="M240 166 L250 157 L260 166 M243 164 V174 H257 V164"/>
      </g>
    </svg>
    <div class="person">
      <div class="person__name">Dana Melbrook</div>
      <div class="person__title">Principal</div>
    </div>
    <ul class="contact">
      <li>www.vktadvisory.com</li>
      <li>hello.vkt@advisory.com</li>
      <li>415-555-0178</li>
      <li>14 Harlow Lane Westbury</li>
      <li>NSW 2199</li>
    </ul>
  </div>
</section>

<section class="card card--back" aria-label="Business card back">
  <div class="back__company">VKT Consulting</div>
</section>

</body>
</html>
```